Website for Reiki and Wellness Courses

I teach online courses in Reiki and wellness/self-development and am needing a new website.

The focus of the website will be to provide descriptions of the courses as well as include a blog and pages where students in my courses will visit for additional information.

Note: courses are NOT hosted on this site.
The focus of this website will be to encourage viewers to enroll in courses as well as opt in to the email list.

I will upload copy soon. My old website is: http://brightfernstudies.example. Please do not use existing logo.

Target Market(s)

Alternative health, wellness, spirituality, personal development. Males and females of all ages seeking to improve their health and life.

Industry/Entity Type

Health And Wellness

Logo Text

No text (please do not use existing logo)

Coding

Coded - Design and coding required

Number of Pages Required

5+ page

Requirements
Must have
• 1. Home page
• 2. About page
• 3. Courses page that outlines courses (there are currently 6 courses with 1 coming soon)
• 4. Individual course page (maybe a template that I can adjust color and pictures for with each course)
• 5. Blog
• 6. Student Area that outlines all Student Areas
• 7. Individual Student Area page (maybe a template that I can adjust color and pictures for with each course)
• 8. Shop page (note: items will not currently be purchased through website - it will be a link to quillmarket for a book).
• 9. Student thank-you page (maybe a template that I can adjust color and pictures for with each course) this is the page students are directed to at end of course with vouchers for other courses.
• Opt-in for the home page, course pages, blog and thank-you pages
Nice to have
• I would like the design to be calm, clean and soothing. Ideally visitors feel relaxed when viewing the site and are encouraged to explore the courses, subscribe to the email list and purchase a product.
• ~ Testimonials page
• ~ Contact page
• I tend to gravitate towards blues, greys and purples as well as monochromatic color schemes.
Should not have
• Contact form on home page
• phone number on home page
• location/physical address
• dates for blog posts

```html
<!DOCTYPE html>
<html lang="en">
<head>
<meta charset="utf-8">
<title>Bright Fern Studies</title>
<link href="https://fonts.googleapis.com/css2?family=Raleway:wght@400;500;600;700&family=Open+Sans:ital,wght@0,400;0,600;1,400&family=Lora:ital@1&display=swap" rel="stylesheet">
<style>
:root{
  --purple:#9b3d98;
  --purple-dark:#7f2f86;
  --blue:#2e4a9e;
  --teal:#2bb3c4;
  --green:#6ac16a;
  --orange:#f0954a;
  --pink:#e2457f;
  --text:#555;
  --grey-bg:#f2f2f2;
  --footer:#6d7189;
  --footer-dark:#5b5f76;
  --white:#fff;
}
*{box-sizing:border-box;margin:0;padding:0}
html,body{width:1200px;height:3913px;overflow:hidden}
body{font-family:"Open Sans",Arial,sans-serif;color:var(--text);background:var(--white);font-size:15px}
a{text-decoration:none}
.section-title{font-family:"Raleway",sans-serif;font-weight:400;font-size:42px;text-align:center;letter-spacing:1px}
.section-title b{font-weight:700}
.btn{display:inline-block;font-family:"Raleway",sans-serif;font-size:19px;padding:0 22px;height:50px;line-height:46px;border:2px solid currentColor;text-align:center;text-decoration:none}

/* header */
.site-header{height:104px;display:flex;align-items:center;justify-content:space-between;padding:0 60px 0 78px}
.brand{display:flex;align-items:center;gap:14px;font-family:"Raleway",sans-serif;font-weight:600;font-size:20px;color:var(--purple-dark);letter-spacing:.5px}
.brand-dot{width:52px;height:52px;border-radius:50%;background:var(--purple)}
.main-nav{display:flex;height:104px}
.main-nav a{font-family:"Raleway",sans-serif;font-size:17px;color:#888;padding:0 22px;line-height:100px}
.main-nav a.active{color:var(--purple);border-bottom:4px solid var(--purple)}

/* hero */
.hero{position:relative;height:574px;background:linear-gradient(180deg,#eef3f6 0%,#dfe9ef 50%,#c7c0b4 78%,#a79c8d 100%)}
.hero-content{position:absolute;left:78px;top:160px;width:640px}
.hero-title{font-family:"Raleway",sans-serif;font-weight:500;font-size:50px;line-height:58px;color:var(--purple-dark)}
.hero-sub{font-family:"Lora",serif;font-style:italic;font-size:18px;color:#444;margin:18px 0 22px;line-height:28px}
.hero .btn{background:var(--blue);color:#fff;border-color:var(--blue);height:58px;line-height:54px;width:197px}
.hero-dots{position:absolute;left:80px;top:450px;display:flex;gap:12px}
.hero-dots span{width:10px;height:10px;border-radius:50%;background:#fff;opacity:.7}

/* welcome */
.welcome{height:260px;background:var(--purple);color:#fff;text-align:center;padding-top:52px}
.welcome .section-title{font-size:40px}
.welcome p{width:1000px;margin:16px auto 0;font-size:14px;line-height:28px}
.welcome svg{margin-top:6px}

/* courses */
.courses{height:957px;padding-top:55px}
.courses .section-title{color:var(--purple-dark)}
.intro{width:900px;margin:20px auto 0;text-align:center;font-size:14px;line-height:26px}
.course-grid{display:grid;grid-template-columns:repeat(3,322px);column-gap:38px;margin:38px 0 0 78px}
.course{text-align:center;height:372px}
.course-photo{height:188px}
.course h3{font-family:"Raleway",sans-serif;font-weight:500;font-size:17px;line-height:28px;height:60px;margin-top:24px;text-transform:uppercase}
.course .btn{margin-top:12px}
.c1 h3{color:var(--blue)}.c1 .btn{background:var(--blue);color:#fff;border-color:var(--blue)}
.c2 h3,.c2 .btn{color:var(--teal)}
.c3 h3,.c3 .btn{color:var(--green)}
.c4 h3,.c4 .btn{color:var(--orange)}
.c5 h3,.c5 .btn{color:var(--pink)}
.c6 h3,.c6 .btn{color:var(--purple)}

/* blog */
.blog{height:583px;background:var(--grey-bg);padding-top:52px}
.blog .section-title{color:var(--blue)}
.blog-grid{display:grid;grid-template-columns:499px 499px;column-gap:45px;margin:30px 0 0 78px}
.blog-photo{height:198px}
.blog-post h3{font-family:"Raleway",sans-serif;font-weight:500;font-size:19px;color:var(--blue);line-height:28px;margin-top:16px}
.blog-post p{font-size:14px;line-height:26px;margin-top:12px}

/* student areas */
.student-areas{position:relative;height:479px;overflow:hidden}
.student-mandala{position:absolute;left:470px;top:40px;width:400px;height:400px;border-radius:50%;background:radial-gradient(circle,#d9c8ee 0%,#e9def5 40%,rgba(255,255,255,0) 70%)}
.student-photo{position:absolute;left:700px;top:40px;width:380px;height:439px;background:linear-gradient(180deg,#f4f2f2,#e4e0e2 60%,#d8d3d6)}
.student-content{position:absolute;left:156px;top:56px;z-index:2}
.student-content .section-title{text-align:left;color:var(--blue)}
.student-content .section-title b{color:var(--purple)}
.area-list{list-style:none;margin-top:20px}
.area-list li{display:flex;align-items:center;gap:12px;font-size:15px;height:32px;color:#666}
.area-list li::before{content:"";width:16px;height:16px;border-radius:50%;background:var(--purple);opacity:.8}
.student-content .btn{margin-top:16px;background:var(--green);color:#fff;border-color:var(--green);width:258px;height:56px;line-height:52px}

/* newsletter band */
.inspired{height:296px;background:var(--blue);color:#fff;text-align:center;padding-top:50px}
.inspired p{font-size:14px;line-height:26px;margin-top:14px}
.signup{display:flex;justify-content:center;gap:12px;margin-top:28px}
.signup input{width:236px;height:52px;border:0;padding:0 16px;font-size:14px;font-family:inherit}
.signup button{width:236px;height:52px;background:transparent;color:#fff;border:2px solid #fff;font-family:"Raleway",sans-serif;font-size:19px}

/* testimonials */
.testimonials{height:340px;padding-top:56px}
.testimonials .section-title{color:var(--blue)}
.testimonials .section-title b{color:var(--purple)}
.quotes{display:grid;grid-template-columns:500px 500px;column-gap:45px;margin:44px 0 0 78px}
.quote{display:flex;gap:24px}
.quote-photo{width:106px;height:106px;flex:none;background:linear-gradient(135deg,#d9d4cf,#b9b0a9)}
.quote p{font-size:14px;line-height:24px;color:#777}
.quote cite{display:block;margin-top:14px;font-family:"Raleway",sans-serif;font-weight:700;font-style:italic;font-size:17px;color:#444}
.quote-dots{display:flex;justify-content:center;gap:8px;margin-top:28px}
.quote-dots span{width:10px;height:10px;border-radius:50%;background:#9aa0b8}

/* footer */
.site-footer{height:262px;background:var(--footer);color:#fff;display:grid;grid-template-columns:260px 260px 275px 260px;padding:28px 0 0 78px;font-size:13px}
.site-footer h4{font-family:"Raleway",sans-serif;font-weight:700;font-size:17px;margin-bottom:16px}
.sitemap a{display:block;color:#fff;line-height:22px}
.contact-row{display:flex;gap:14px;margin-bottom:14px;line-height:20px;align-items:flex-start}
.contact-row svg{flex:none;margin-top:3px}
.newsletter p{line-height:20px;width:245px}
.newsletter input{width:245px;height:42px;border:0;margin-top:12px;padding:0 12px;font-size:13px;font-family:inherit}
.newsletter button{margin-top:12px;width:168px;height:48px;background:transparent;color:#fff;border:2px solid #fff;font-family:"Raleway",sans-serif;font-size:18px}
.social a{display:flex;align-items:center;gap:14px;color:#fff;margin-bottom:12px}
.social a span{width:46px;height:46px;border-radius:50%;border:2px solid #fff}
.copyright{height:58px;background:var(--footer-dark);color:#fff;text-align:center;line-height:58px;font-size:13px}
</style>
</head>
<body>

<header class="site-header">
  <div class="brand"><span class="brand-dot"></span>BRIGHT FERN STUDIES</div>
  <nav class="main-nav">
    <a class="active" href="#">HOME</a><a href="#">ABOUT</a><a href="#">COURSES</a><a href="#">BLOG</a><a href="#">STUDENT AREAS</a><a href="#">CONTACT</a>
  </nav>
</header>

<section class="hero" role="img" aria-label="Woman meditating in lotus pose on a pebble beach by the sea">
  <div class="hero-content">
    <h1 class="hero-title">Become a Certified USUI Reiki Master</h1>
    <p class="hero-sub">This comprehensive online course gives you all of the tools you need to be certified as a Traditional Usui Reiki Master.</p>
    <a class="btn" href="#">KNOW MORE</a>
  </div>
  <div class="hero-dots"><span></span><span></span><span></span></div>
</section>

<section class="welcome">
  <h2 class="section-title">WELCOME TO <b>BRIGHT FERN STUDIES</b></h2>
  <p>Thought to be centuries old and rediscovered in the late 1800's, Reiki (pronounced ray-key) is a healing and enlightenment system. Reiki can be translated into "Universal (Rei) Life Energy (Ki)". As a practitioner of Reiki, you attune your awareness to this energy and utilize it for the physical and emotional healing of self and others.</p>
  <svg width="22" height="22" viewBox="0 0 22 22" fill="none" stroke="#fff" stroke-width="2"><path d="M5 4l6 6 6-6M5 11l6 6 6-6"/></svg>
</section>

<section class="courses">
  <h2 class="section-title">OUR <b>COURSES</b></h2>
  <p class="intro">Online learning gives you the opportunity to tailor your course to meet your needs. If you are very interested in a specific topic, you can spend more time on it, research connections and reflect on how it applies to your every day life.</p>
  <div class="course-grid">
    <article class="course c1"><div class="course-photo" role="img" aria-label="Woman stretching on a sunlit beach" style="background:linear-gradient(180deg,#f3f0c8,#b9d3b0 60%,#8bb0a8)"></div><h3>Reiki Level I, II Master<br>Certification</h3><a class="btn" href="#">READ MORE</a></article>
    <article class="course c2"><div class="course-photo" role="img" aria-label="Woman with a white horse" style="background:linear-gradient(180deg,#c7d9b9,#8fb483 60%,#6e8f65)"></div><h3>Animal Reiki Practitioner<br>Certification</h3><a class="btn" href="#">READ MORE</a></article>
    <article class="course c3"><div class="course-photo" role="img" aria-label="Crystals placed on a relaxing person" style="background:linear-gradient(180deg,#9a8f84,#c8b6a2 50%,#6f6459)"></div><h3>Crystak Reiki Practitioner<br>Certification</h3><a class="btn" href="#">READ MORE</a></article>
    <article class="course c4"><div class="course-photo" role="img" aria-label="Happy woman at a laptop" style="background:linear-gradient(180deg,#dbe8f4,#eef3f7 60%,#b9c7d6)"></div><h3>Build Your Reiki Business</h3><a class="btn" href="#">READ MORE</a></article>
    <article class="course c5"><div class="course-photo" role="img" aria-label="Woman sitting at sunset looking at the horizon" style="background:linear-gradient(180deg,#f7efe2,#f1dcc0 60%,#d6b99a)"></div><h3>Acupressure and Reiki for<br>Anxiety and Depression</h3><a class="btn" href="#">READ MORE</a></article>
    <article class="course c6"><div class="course-photo" role="img" aria-label="Woman with open arms facing a bright sky" style="background:linear-gradient(180deg,#b9d1e8,#dce9f4 60%,#c0d6e6)"></div><h3>Your Soul is Calling</h3><a class="btn" href="#">READ MORE</a></article>
  </div>
</section>

<section class="blog">
  <h2 class="section-title">LATEST <b style="color:var(--purple)">BLOG</b></h2>
  <div class="blog-grid">
    <article class="blog-post">
      <div class="blog-photo" role="img" aria-label="Stacked pebbles on a pastel beach" style="background:linear-gradient(180deg,#f1d7d9,#e7c9cf 50%,#c9a6a7)"></div>
      <h3>can you let me know if I would be attuned to the Karuna symbol of Zonar and Harth?</h3>
      <p>The symbols are included in the manuals so they are a part of the consciousness of the course and can be used. I do not specifically include them in the ceremony but because you are introduced</p>
    </article>
    <article class="blog-post">
      <div class="blog-photo" role="img" aria-label="Stacked stones on raked sand" style="background:linear-gradient(180deg,#e3ddd4,#cfc6ba 50%,#b2a899)"></div>
      <h3>can you let me know if I would be attuned to the Karuna symbol of Zonar and Harth?</h3>
      <p>The symbols are included in the manuals so they are a part of the consciousness of the course and can be used. I do not specifically include them in the ceremony but because you are introduced</p>
    </article>
  </div>
</section>

<section class="student-areas">
  <div class="student-mandala" role="img" aria-label="Soft pastel mandala glow"></div>
  <div class="student-photo" role="img" aria-label="Woman in white meditating in profile"></div>
  <div class="student-content">
    <h2 class="section-title">STUDENT <b>AREAS</b></h2>
    <ul class="area-list">
      <li>Reiki Level I, II Master Certification</li>
      <li>Animal Reiki Practitioner Certification</li>
      <li>Crystak Reiki Practitioner Certification</li>
      <li>Build Your Reiki Business</li>
      <li>Acupressure and Reiki for Anxiety and Depression</li>
      <li>Your Soul is Calling</li>
      <li>Sacred Sound and Breath</li>
    </ul>
    <a class="btn" href="#">BOOK YOUR COURSE</a>
  </div>
</section>

<section class="inspired">
  <h2 class="section-title">STAY <b>INSPIRED</b></h2>
  <p>Receive information and articles each month to keep you feeling inspired. As a thank-you, you will also receive access to soothing music<br>you can download for use in your Reiki sessions and meditation.</p>
  <form class="signup">
    <input type="text" placeholder="First Name*"><input type="text" placeholder="Last Name*"><input type="email" placeholder="Email Id*">
    <button type="button">YES-COUNT ME IN</button>
  </form>
</section>

<section class="testimonials">
  <h2 class="section-title">WHAT OUR <b>CLIENT SAY</b></h2>
  <div class="quotes">
    <figure class="quote"><div class="quote-photo" role="img" aria-label="Portrait of a client"></div><blockquote><p>" I was drawn to this course with the desire to heal family, friends and pets and this course has given me that ability and more... "</p><cite>Dana Whitfield</cite></blockquote></figure>
    <figure class="quote"><div class="quote-photo" role="img" aria-label="Portrait of a client"></div><blockquote><p>" I am in LOVE with this course. Not only is it packed with lots of information to guide you toward understanding and appreciating Reiki... "</p><cite>Mara Ellison</cite></blockquote></figure>
  </div>
  <div class="quote-dots"><span></span><span></span><span></span></div>
</section>

<footer class="site-footer">
  <div class="sitemap">
    <h4>SITEMAP</h4>
    <a href="#">Home</a><a href="#">About Us</a><a href="#">Courses</a><a href="#">Blog</a><a href="#">Student areas</a><a href="#">Contact</a>
  </div>
  <div class="contact">
    <h4>GET IN TOUCH</h4>
    <div class="contact-row"><svg width="16" height="18" viewBox="0 0 16 18" fill="#fff"><path d="M8 0a6 6 0 0 0-6 6c0 4.5 6 12 6 12s6-7.5 6-12a6 6 0 0 0-6-6zm0 8.5A2.5 2.5 0 1 1 8 3.5a2.5 2.5 0 0 1 0 5z"/></svg><div><b>BRIGHT FERN STUDIES</b><br>101- lorem ipsum is simple text is dummy text of printing &amp; type settig industry</div></div>
    <div class="contact-row"><svg width="16" height="12" viewBox="0 0 16 12" fill="#fff"><path d="M0 0h16v12H0z"/><path d="M0 0l8 6 8-6" stroke="#6d7189" stroke-width="1.5" fill="none"/></svg>info@brightfernstudies.example</div>
  </div>
  <div class="newsletter">
    <h4>NEWSLETTER</h4>
    <p>Would you like to receive exclusive access to articles, white papers and our regular monthly newsletter?</p>
    <input type="email" placeholder="Email Id">
    <button type="button">SUBSCRIBE</button>
  </div>
  <div class="social">
    <h4>FOLLOW US</h4>
    <a href="#"><span></span>Friendbook</a>
    <a href="#"><span></span>Circleplus</a>
    <a href="#"><span></span>Chirper</a>
  </div>
</footer>
<div class="copyright">©BRIGHT FERN STUDIES - 2016 All rights reserved.</div>

</body>
</html>
```